Redesign of Form/Document Navigation Page

I need a redesign of our document and navigation bar on the left. We want the same navigation bar layout/setup but want the buttons and typography to be simple and matching all over. The form needs to be aesthetically pleasing and fit within the page.

1st attachment is our Direct Deposit and the second is the form continued.

```html
<!DOCTYPE html>
<html lang="en">
<head>
<meta charset="utf-8">
<title>Employee Direct Deposit Enrollment Form</title>
<link href="https://fonts.googleapis.com/css2?family=Open+Sans:wght@300;400;600&family=Raleway:wght@500;700;800&display=swap" rel="stylesheet">
<style>
:root{
  --gold:#f0b323;
  --gold-dark:#d99c10;
  --ink:#222;
  --text:#555;
  --muted:#888;
  --line:#cfcfcf;
  --side:#ececec;
  --side-line:#dcdcdc;
  --white:#fff;
  --icon:#4a4f5a;
}
*{box-sizing:border-box;margin:0;padding:0}
html,body{width:1200px;height:1023px;overflow:hidden;background:var(--white);font-family:"Open Sans",sans-serif;color:var(--text)}
.topbar{position:absolute;left:0;top:0;width:1200px;height:66px;border-bottom:1px solid #e2e2e2;display:flex;align-items:center}
.brand{position:absolute;left:40px;top:14px;display:flex;align-items:center;gap:8px}
.brand-dot{width:34px;height:34px;border-radius:50%;background:#27346b}
.brand-name{font-family:"Raleway",sans-serif;font-weight:800;color:var(--gold);font-size:18px;line-height:19px;text-transform:uppercase;width:170px}
.btn-back{position:absolute;left:297px;top:18px;height:31px;width:124px;background:var(--gold);color:#fff;font-size:12px;display:flex;align-items:center;justify-content:center;gap:6px;border-radius:2px}
.nav-link{position:absolute;top:22px;display:flex;align-items:center;gap:8px;font-size:13px;color:#444}
.nav-home{left:448px}.nav-help{left:536px}
.user{position:absolute;left:962px;top:13px;display:flex;align-items:center;gap:9px;font-size:13.5px;color:#333}
.avatar{width:40px;height:40px;border-radius:50%;background:radial-gradient(circle at 50% 40%,#e3b99d,#8a6a55)}
.power{position:absolute;left:1133px;top:19px}
.sidebar{position:absolute;left:0;top:67px;width:290px;border-right:1px solid var(--side-line)}
.side-item{height:79px;background:var(--side);border-bottom:1px solid var(--side-line);display:flex;align-items:center;padding-left:25px;gap:13px;font-family:"Raleway",sans-serif;font-weight:500;font-size:14.5px;color:#444}
.side-item.active{background:var(--gold);color:#fff}
.side-icon{width:50px;height:50px;border-radius:50%;background:#fff;border:1px solid #d8d8d8;display:flex;align-items:center;justify-content:center}
.main{position:absolute;left:348px;top:0;width:800px}
.page-title{position:absolute;top:104px;font-weight:400;font-size:27px;color:var(--ink);white-space:nowrap}
.intro{position:absolute;top:155px;width:795px;font-size:12.5px;line-height:24px;color:#666}
.attach-title{position:absolute;top:276px;font-size:16px;color:var(--ink)}
.btn-refresh{position:absolute;top:315px;width:110px;height:41px;background:var(--gold);color:#fff;font-size:14.5px;display:flex;align-items:center;justify-content:center;gap:8px;border-radius:2px}
.panel{position:absolute;left:349px;top:403px;width:793px;height:520px;border:1px solid var(--line);padding:28px 42px}
.panel h2{font-weight:300;font-size:28px;color:var(--ink);margin-bottom:10px}
.note{font-size:12.5px;color:#666;margin-bottom:16px}
.note-strong{font-size:13.5px;color:var(--ink);margin-bottom:12px}
.notify{font-size:12.5px;color:#666;text-transform:uppercase;margin-bottom:21px}
.notify b{color:var(--gold);font-weight:400}
.radio-row{display:flex;gap:34px;font-size:13px;color:#333;margin-left:3px}
.radio{display:flex;align-items:center;gap:7px}
.radio i{width:15px;height:15px;border:1px solid #999;border-radius:50%;display:inline-block}
.fields{display:grid;grid-template-columns:216px 216px 216px;column-gap:16px;row-gap:17px;margin-top:24px;margin-left:3px}
.field{height:35px;border:1px solid #c6c6c6;font-size:13px;color:#999;padding:0 12px;display:flex;align-items:center}
.radio-pair{display:flex;gap:37px;align-items:center;font-size:13px;color:#333;padding-left:3px}
.amount{display:flex;justify-content:flex-end;align-items:center;gap:12px;margin-top:15px;margin-right:61px;font-size:13.5px;color:#222}
.amount-box{width:51px;height:31px;background:var(--gold);color:#fff;display:flex;align-items:center;justify-content:center;font-size:13.5px}
.important{margin-top:45px;font-size:13.5px;color:var(--ink)}
.auth{margin-top:12px;font-size:11.5px;line-height:22px;color:#666}
.footer{position:absolute;left:0;top:984px;width:1200px;border-top:1px solid #e2e2e2;height:39px;font-size:11.5px;color:#666;text-align:center;padding-top:11px}
.footer .ver{position:absolute;right:15px;top:11px}
</style>
</head>
<body>
<header class="topbar">
  <div class="brand"><span class="brand-dot"></span><span class="brand-name">Keystone Patrol Services</span></div>
  <div class="btn-back"><svg width="16" height="12" viewBox="0 0 16 12" fill="none" stroke="#fff" stroke-width="1.4"><path d="M6 1 1 5.5 6 10M1 5.5h8a6 6 0 0 1 6 6"/></svg>Back to Profile</div>
  <div class="nav-link nav-home"><svg width="20" height="18" viewBox="0 0 20 18" fill="none" stroke="#f0b323" stroke-width="1.4"><path d="M1 9 10 1l9 8M4 7v10h4v-5h4v5h4V7"/></svg>Home</div>
  <div class="nav-link nav-help"><svg width="20" height="20" viewBox="0 0 20 20" fill="none" stroke="#f0b323" stroke-width="1.4"><circle cx="10" cy="10" r="8.5"/><path d="M10 8v6M10 5v1.5"/></svg>Help</div>
  <div class="user"><span class="avatar" role="img" aria-label="User profile photo"></span>Dana Wells<svg width="10" height="6" viewBox="0 0 10 6" fill="none" stroke="#555" stroke-width="1.2"><path d="m1 1 4 4 4-4"/></svg></div>
  <svg class="power" width="32" height="32" viewBox="0 0 32 32" fill="none" stroke="#f0b323" stroke-width="2.2" stroke-linecap="round"><path d="M10 7a12 12 0 1 0 12 0M16 3v12"/></svg>
</header>

<nav class="sidebar">
  <div class="side-item active"><span class="side-icon"><svg width="26" height="26" viewBox="0 0 26 26" fill="#f0b323"><path d="M13 1v9M9 6l4 4 4-4" stroke="#f0b323" stroke-width="2" fill="none"/><ellipse cx="8" cy="15" rx="6" ry="2.5"/><ellipse cx="8" cy="20" rx="6" ry="2.5"/><ellipse cx="18" cy="17" rx="6" ry="2.5"/><ellipse cx="18" cy="22" rx="6" ry="2.5"/></svg></span>Direct Deposit</div>
  <div class="side-item"><span class="side-icon"><svg width="26" height="26" viewBox="0 0 26 26" fill="none" stroke="#4a4f5a" stroke-width="2.4"><path d="M5 8a9 9 0 0 0 0 10M21 8a9 9 0 0 1 0 10M16 9h-4a2 2 0 0 0 0 4h2a2 2 0 0 1 0 4h-4M13 6v14"/></svg></span>Change W-4</div>
  <div class="side-item"><span class="side-icon"><svg width="26" height="26" viewBox="0 0 26 26" fill="none" stroke="#4a4f5a" stroke-width="2"><path d="M3 4v18M7 4v10M22 4v18"/><circle cx="14" cy="13" r="5"/><path d="m10 17-5 5"/></svg></span>Labour Code</div>
  <div class="side-item"><span class="side-icon"><svg width="26" height="26" viewBox="0 0 26 26" fill="#4a4f5a"><circle cx="8" cy="9" r="4"/><path d="M1 20a7 6 0 0 1 14 0z"/><rect x="15" y="7" width="9" height="2"/><rect x="15" y="12" width="9" height="2"/><rect x="17" y="17" width="7" height="2"/></svg></span>Personal Information</div>
  <div class="side-item"><span class="side-icon"><svg width="26" height="26" viewBox="0 0 26 26" fill="#4a4f5a"><circle cx="13" cy="5" r="3"/><circle cx="5" cy="14" r="3"/><circle cx="21" cy="14" r="3"/><path d="M1 24a4 4 0 0 1 8 0zM17 24a4 4 0 0 1 8 0zM10 12h6v6h-6z"/></svg></span>Appraisal and Review</div>
  <div class="side-item"><span class="side-icon"><svg width="26" height="26" viewBox="0 0 26 26" fill="none" stroke="#4a4f5a" stroke-width="1.8"><rect x="2" y="10" width="20" height="12"/><path d="M5 14h7M5 18h6M14 12 23 3M17 20h3"/></svg></span>Write Up-Slip</div>
  <div class="side-item"><span class="side-icon"><svg width="26" height="26" viewBox="0 0 26 26" fill="none" stroke="#4a4f5a" stroke-width="1.6"><path d="M2 22 22 4M7 22v-3M11 22v-6M15 22v-9M19 22v-12M23 22V7"/></svg></span>Employee Performance</div>
</nav>

<main class="main">
  <h1 class="page-title">Employee Direct Deposit Enrollment Form</h1>
  <p class="intro">To enroll in Direct Deposit, simply fill out this form. Attach a voided check for each checking account - not a deposit slip. If depositing to a savings account, ask your bank to give you the Routing/Transit Number for your account. It isn't always the same as the number on a savings deposit slip. This will help ensure that you are paid correctly. Once filled out, accounting will review your information for processing. Once processed, you will receive an email confirmation with details.</p>
  <h3 class="attach-title">Attach A Voided Check Or Bank Deposit Form for the Account</h3>
  <div class="btn-refresh"><svg width="18" height="18" viewBox="0 0 18 18" fill="none" stroke="#fff" stroke-width="1.8"><path d="M14 4a7 7 0 1 1-5-2M9 0v4h4"/></svg>Refresh</div>
</main>

<section class="panel">
  <h2>Account Information</h2>
  <p class="note">The last item must be for the remaining amount owed to you. To distribute to more accounts, please complete another form.</p>
  <p class="note-strong">Make sure to indicate what kind of account, along with enrolling or declining.</p>
  <p class="notify"><b>**</b>Notify payroll immediately if you close or change bank account<b>**</b></p>
  <div class="radio-row">
    <span class="radio"><i></i>New Enrollment</span>
    <span class="radio"><i></i>Change Enrollment</span>
    <span class="radio"><i></i>Cancel Enrollment</span>
  </div>
  <div class="fields">
    <div class="field">Bank name</div>
    <div class="field">City</div>
    <div class="field">State</div>
    <div class="field">Routing Transit</div>
    <div class="field">Account Number</div>
    <div class="radio-pair"><span class="radio"><i></i>Checking</span><span class="radio"><i></i>Savings</span></div>
  </div>
  <div class="amount">Amount <span class="amount-box">100</span> %</div>
  <p class="important">IMPORTANT! Please read and sign before completing and submitting.</p>
  <p class="auth">I hereby authorize KEYSTONE PATROL SERVICES to deposit any amounts owed me, as instructed by my employer, by initiating credit entries to my account at the financial institution (hereinafter "Bank") indicated on this form. Further, I authorize Bank to accept and to credit any credit entries indicated by KEYSTONE PATROL</p>
</section>

<footer class="footer">Copyright © 2016. Keystone Patrol Services. All Rights Reserved<span class="ver">C8</span></footer>
</body>
</html>
```